Tech business card design

We need an amazing business card design for our new business 'Pexla' a marketing tech startup based in Sydney, Australia. We provide an online marketplace for businesses to search and buy advertising media, connect with service providers and learn more about marketing. We wish to communicate 'cool tech', reliability and professionalism and design based around our logo.

Target Market(s)

Business Owners

Contact Information for Business Card

Name
Position
Email Address
Website
Phone Number

Font styles to use
Other font styles liked:
• Avenir & Avenir Next

Colors

Designer to choose colors to be used in the design.

```html
<!DOCTYPE html>
<html lang="en">
<head>
<meta charset="utf-8">
<title>Pexla Business Card</title>
<link rel="stylesheet" href="https://fonts.googleapis.com/css2?family=Nunito+Sans:wght@400;700&display=swap">
<style>
  :root {
    --canvas: #e0dddd;
    --navy: #12133a;
    --card-front: #ffffff;
    --card-back: #dadae6;
  }
  * { margin: 0; padding: 0; box-sizing: border-box; }
  html, body {
    width: 975px;
    height: 1200px;
    overflow: hidden;
    background: var(--canvas);
    font-family: "Nunito Sans", "Avenir Next", sans-serif;
    color: var(--navy);
  }
  .card {
    position: absolute;
    left: 56px;
    width: 864px;
    height: 496px;
    border-radius: 34px;
    overflow: hidden;
  }
  .card--front {
    top: 82px;
    background: var(--card-front);
    border: 1px solid #3a3a3a;
  }
  .card--back {
    top: 631px;
    background: var(--card-back);
  }
  .wordmark {
    position: absolute;
    font-weight: 700;
    font-size: 150px;
    line-height: 1;
    letter-spacing: -2px;
    color: var(--navy);
  }
  .card--front .wordmark { right: 34px; top: 22px; }
  .card--back .wordmark { left: 0; right: 0; top: 150px; text-align: center; }
  .holder {
    position: absolute;
    left: 31px;
    top: 205px;
  }
  .holder__name { font-size: 29px; font-weight: 700; line-height: 1.15; }
  .holder__role { font-size: 24px; font-weight: 400; line-height: 1.3; }
  .divider {
    position: absolute;
    left: 31px;
    top: 288px;
    width: 802px;
    height: 2px;
    background: var(--navy);
  }
  .contacts {
    position: absolute;
    left: 31px;
    top: 310px;
    list-style: none;
    font-size: 21px;
    line-height: 32px;
  }
  .contacts li { display: flex; align-items: center; gap: 8px; }
  .contacts svg { width: 21px; height: 21px; flex: none; }
  .address {
    position: absolute;
    right: 31px;
    top: 325px;
    font-size: 21px;
    line-height: 29px;
    font-style: normal;
  }
  .swoosh {
    position: absolute;
    left: 0;
    top: 0;
    width: 100%;
    height: 100%;
  }
  .site-url {
    position: absolute;
    left: 0;
    right: 0;
    top: 408px;
    text-align: center;
    font-size: 27px;
    letter-spacing: 4px;
  }
</style>
</head>
<body>
  <section class="card card--front">
    <svg class="swoosh" viewBox="0 0 1056 606" preserveAspectRatio="none" aria-hidden="true">
      <path fill="var(--navy)" d="M0,507 C250,540 600,556 1056,540 L1056,544 C600,562 250,560 0,540 Z"/>
      <path fill="var(--navy)" d="M0,548 C300,570 650,574 1056,550 L1056,606 L0,606 Z"/>
    </svg>
    <div class="wordmark">pexla</div>
    <div class="holder">
      <h1 class="holder__name">JOHN SMITH</h1>
      <p class="holder__role">Position</p>
    </div>
    <div class="divider"></div>
    <ul class="contacts">
      <li>
        <svg viewBox="0 0 24 24" aria-hidden="true"><circle cx="12" cy="12" r="10.5" fill="none" stroke="var(--navy)" stroke-width="2"/><path fill="var(--navy)" d="M8.2 6.5l1.8-.4 1.2 2.8-1.2 1c.6 1.4 1.7 2.5 3.1 3.1l1-1.2 2.8 1.2-.4 1.8c-.2.6-.7 1-1.4 1C10.6 15.6 8.4 13.4 7.2 8c0-.7.4-1.3 1-1.5z"/></svg>
        012-345-6789
      </li>
      <li>
        <svg viewBox="0 0 24 24" aria-hidden="true"><rect x="2" y="5" width="20" height="14" fill="var(--navy)"/><path d="M3 6l9 7 9-7M3 18l7-6M21 18l-7-6" fill="none" stroke="#fff" stroke-width="1.5"/></svg>
        info@pexla.com
      </li>
      <li>
        <svg viewBox="0 0 24 24" aria-hidden="true"><g fill="none" stroke="var(--navy)" stroke-width="1.6"><circle cx="12" cy="12" r="10"/><ellipse cx="12" cy="12" rx="4.5" ry="10"/><path d="M2 12h20M4 7h16M4 17h16M12 2v20"/></g></svg>
        www.pexla.com
      </li>
    </ul>
    <address class="address">Street name City Name,<br>Zipcode,012345</address>
  </section>

  <section class="card card--back">
    <div class="wordmark">pexla</div>
    <p class="site-url">www.pexla.com</p>
  </section>
</body>
</html>
```